Etiketten für Bio Seifen
Zielgruppe
Wir stellen hochwertig 'handgemachte' Bio-Seifen her. Die Zielgruppe ist von 3-99 Jahren und zusätzlich haben wir auch noch Seife für Hunde.
Der Firmenname ist 'Verdolina'
Aufgabenstellung
Das Etikett soll Bezug auf Natur, Bio, Nachhaltigkeit nehmen. Wir stellen uns 'weiche' Aquarellfarben vor...Seife: Lavendel, Calendular, 7 Kräuter etc.
Das Etikett soll auf eine Beutelschachtel. Die Schachtel hat eine Anmaße: Breite 55mm; Höhe 120mm; Tiefe 30mm
Das Etikett soll im vorderen- und hinteren Bereich zusammenhängend geklebt werden.
Das Etikett soll eine Abmaße von: Breite 51mm; Höhe 114mm haben (Vorderseite) Rückseite gleich.
Wir möchten die Produkte auch gerne nummerieren, d.h. jede Seife hat eine Nummer die nicht zu groß dargestellt werden soll aber trotzdem gut leserlich.
Wir haben noch ein paar Bilder hochgeladen wie wir uns das ungefähr vorstellen.

```html
<!DOCTYPE html>
<html lang="de">
<head>
<meta charset="utf-8">
<title>Verdolina – Bio Seife Etikett</title>
<link rel="stylesheet" href="https://fonts.googleapis.com/css2?family=Playball&family=Amatic+SC:wght@400;700&display=swap">
<style>
  :root {
    --page: #ffffff;
    --lavender-pale: #e9e3f3;
    --lavender-soft: #cfc4e5;
    --lavender-mid: #b4a6d8;
    --panel: #a898d0;
    --ink-deep: #563d93;
    --ink-light: #a18fcf;
    --banner: #b9a9dc;
    --leaf: #7fa85a;
    --bloom: #f08a2c;
  }
  html, body {
    margin: 0;
    width: 1200px;
    height: 4521px;
    overflow: hidden;
    background: var(--page);
  }
  .label {
    position: absolute;
    left: 94px;
    top: 60px;
    width: 1003px;
    height: 4406px;
    overflow: hidden;
    background:
      radial-gradient(ellipse 520px 700px at 20% 40%, rgba(255,255,255,.95), rgba(255,255,255,0) 70%),
      radial-gradient(ellipse 600px 500px at 40% 52%, rgba(255,255,255,.9), rgba(255,255,255,0) 70%),
      radial-gradient(ellipse 500px 400px at 10% 80%, rgba(255,255,255,.8), rgba(255,255,255,0) 70%),
      linear-gradient(180deg, var(--lavender-soft) 0%, var(--lavender-pale) 40%, var(--lavender-mid) 100%);
  }
  .back-side {
    position: absolute;
    left: 0;
    top: 0;
    width: 1003px;
    height: 2250px;
    transform: rotate(180deg);
  }
  .info-panel {
    position: absolute;
    left: 111px;
    top: 407px;
    width: 772px;
    height: 1543px;
    background: var(--panel);
    opacity: .9;
  }
  .info-text {
    position: absolute;
    left: 214px;
    top: 560px;
    width: 583px;
    margin: 0;
    font-family: "Playball", cursive;
    font-size: 44px;
    line-height: 63px;
    color: var(--ink-deep);
    text-align: justify;
  }
  .info-text p { margin: 0 0 63px; }
  .back-title {
    position: absolute;
    left: 68px;
    top: 80px;
    width: 420px;
    font-family: "Playball", cursive;
    color: var(--ink-light);
    line-height: 1;
  }
  .back-title .bio { display: block; font-size: 110px; margin-left: 20px; }
  .back-title .seife { display: block; font-size: 220px; margin-top: -60px; }
  .corner-wreath {
    position: absolute;
    left: -120px;
    top: -190px;
    width: 720px;
    height: 720px;
  }
  .front-title {
    position: absolute;
    left: 0;
    top: 2560px;
    width: 1003px;
    font-family: "Playball", cursive;
    line-height: 1;
    text-align: center;
  }
  .front-title .bio {
    display: block;
    font-size: 210px;
    color: var(--ink-deep);
    margin-left: -70px;
  }
  .front-title .seife {
    display: block;
    font-size: 380px;
    color: var(--ink-light);
    margin-top: -110px;
  }
  .herb-wreath {
    position: absolute;
    left: 76px;
    top: 3070px;
    width: 808px;
    height: 808px;
  }
  .banner {
    position: absolute;
    left: 275px;
    top: 4037px;
    width: 514px;
    height: 120px;
  }
  .banner-text {
    position: absolute;
    left: 275px;
    top: 4037px;
    width: 514px;
    height: 120px;
    line-height: 120px;
    text-align: center;
    font-family: "Amatic SC", sans-serif;
    font-weight: 700;
    font-size: 82px;
    letter-spacing: 3px;
    color: var(--ink-deep);
  }
</style>
</head>
<body>
  <div class="label">
    <svg class="corner-wreath" viewBox="0 0 720 720" role="img" aria-label="Aquarell-Kranz aus Lavendel und Ringelblumen">
      <defs>
        <linearGradient id="wreathTone" x1="0" y1="0" x2="1" y2="1">
          <stop offset="0" stop-color="#8fb36a"/>
          <stop offset=".45" stop-color="#7b63b3"/>
          <stop offset=".7" stop-color="#f08a2c"/>
          <stop offset="1" stop-color="#7b63b3"/>
        </linearGradient>
      </defs>
      <circle cx="330" cy="330" r="300" fill="none" stroke="url(#wreathTone)" stroke-width="60" opacity=".75"/>
    </svg>

    <div class="back-side">
      <div class="info-panel"></div>
      <div class="info-text">
        <p>Lorem ipsum dolor sit amet, consectetur adipiscing elit, sed do eiusmod tempor incididunt ut labore et dolore magna aliqua. Quis ipsum suspendisse ultrices gravida. Risus commodo viverra maecenas accumsan lacus vel facilisis.</p>
        <p>Lorem ipsum dolor sit amet, consectetur adipiscing elit, sed do eiusmod tempor incididunt ut labore et dolore</p>
      </div>
      <div class="back-title"><span class="bio">Bio</span><span class="seife">Seife</span></div>
    </div>

    <div class="front-title"><span class="bio">Bio</span><span class="seife">Seife</span></div>

    <svg class="herb-wreath" viewBox="0 0 808 808" role="img" aria-label="Aquarell-Kräuterkranz mit Lavendel und Ringelblumen um ein gezeichnetes Stück handgemachte Seife">
      <defs>
        <linearGradient id="herbTone" x1="0" y1="0" x2="1" y2="1">
          <stop offset="0" stop-color="#f08a2c"/>
          <stop offset=".35" stop-color="#7b63b3"/>
          <stop offset=".7" stop-color="#86b060"/>
          <stop offset="1" stop-color="#f08a2c"/>
        </linearGradient>
      </defs>
      <circle cx="404" cy="404" r="340" fill="none" stroke="url(#herbTone)" stroke-width="70" opacity=".75"/>
      <rect x="250" y="230" width="300" height="370" rx="20" fill="#d9d3ec" opacity=".8"/>
    </svg>

    <svg class="banner" viewBox="0 0 514 120" aria-hidden="true">
      <path d="M0 0 H514 L494 60 L514 120 H0 L20 60 Z" fill="var(--banner)"/>
    </svg>
    <div class="banner-text">MIT KRÄUTERN</div>
  </div>
</body>
</html>
```